PlayTallyCollective - Game Statistics and Achievement Tracking

I need a new modern design for an existing website.

The website is a project to track statistics and achievements for games (currently Vaporn Achievements/Stats and stats for Cargo Haul Odyssey 2 and Frontier Rig Journeys).
I am currently expanding the site with other platforms (like QVR) and more games.
I am also adding a user registration/signin with user profiles to show off their achievements and stats across all platforms and games.

The current website is available at https://plytly.example/
To search for data you can use the username "pixelornin" (without quotes).

The design should be modern and extendable and contain space for a logo.

The logo should match the project. It should combine Gaming with statistics.

Target Market(s)

Video game players

Number of Pages Required

5+ page

Font styles to use
Sans Serif

Requirements
Must have
• Basic Layout, User profile page (not yet available on live site), Search Page for Platforms/Games, Platform profile page, Dark theme

```html
<!DOCTYPE html>
<html lang="en">
<head>
<meta charset="utf-8">
<title>PlayTallyCollective – Track Your Gaming Achievements &amp; Stats</title>
<link href="https://fonts.googleapis.com/css2?family=Outfit:wght@400;500;600&family=Poppins:wght@400;500;700&display=swap" rel="stylesheet">
<style>
:root{
  --ink:#ffffff;
  --dark:#1a1c22;
  --purple:#241f45;
  --live:#ff0000;
  --card:#ffffff;
  --card-ink:#1a1a1a;
  --card-muted:#555;
  --icon:#d8262c;
  --cyan:#77ffff;
  --yellow:#ffdd00;
  --pink:#ff2a7a;
  --green:#10ff1c;
}
*{box-sizing:border-box;margin:0;padding:0}
html,body{width:684px;height:1200px;overflow:hidden}
body{position:relative;background:var(--purple);font-family:"Poppins",sans-serif;color:var(--ink)}
.abs{position:absolute}
.topbar{left:0;top:0;width:684px;height:43px;background:linear-gradient(90deg,#b0101a 0%,#3a1d7a 25%,#0b3aa0 45%,#12707a 65%,#2a8a2a 80%,#a88a10 100%)}
.live{left:64px;top:0;width:76px;height:43px;background:var(--live);text-align:center;font-weight:700;font-size:12px;padding-top:15px}
.live svg{position:absolute;left:10px;top:3px}
.region{top:13px;width:62px;height:17px;border:1px solid #fff;border-radius:9px;font-size:8px;text-align:center;line-height:15px}
.hero{left:0;top:43px;width:684px;height:314px;background:
  radial-gradient(ellipse at 75% 45%,#5a4a42 0%,#2f3a48 30%,transparent 60%),
  linear-gradient(180deg,#3a2a55 0%,#263a5a 45%,#34304e 80%,#1a1c22 100%)}
.nav{top:21px;left:0;width:684px;height:43px}
.logo{left:54px;top:53px;display:flex;align-items:center;gap:8px;font-family:"Outfit",sans-serif;font-weight:600;font-size:17px}
.logo i{display:block;width:22px;height:22px;border-radius:50%;background:#2bd46a}
.menu{top:59px;font-size:8px}
.icons{top:55px;left:552px;display:flex;gap:11px}
.headline{left:54px;top:130px;font-family:"Outfit",sans-serif;font-size:29px;line-height:40px;font-weight:400}
.headline b{font-weight:600}
.lead{left:54px;top:209px;width:320px;font-size:8.8px;line-height:13.6px}
.btn{height:30px;width:120px;font-weight:700;font-size:9px;text-align:center;line-height:30px;
  background:linear-gradient(90deg,#d41010 0 4px,#4f8cf5 4px,#a070f0 60%,#f040d0 100%);
  clip-path:polygon(0 0,88% 0,100% 45%,100% 100%,0 100%)}
.side{top:169px;width:21px;height:76px;background:rgba(255,255,255,.18)}
.side svg{position:absolute;left:4px;top:30px}
.features{left:0;top:357px;width:684px;height:428px;background:var(--dark)}
.h2{width:684px;text-align:center;font-family:"Outfit",sans-serif;font-size:21px;font-weight:400}
.h2 b{font-weight:600}
.frame{top:459px;width:132px;height:110px;border:1px solid #bbb}
.shot{top:470px;width:133px;height:110px}
.fcard{top:553px;width:101px;height:119px;background:var(--card);border-radius:6px;color:var(--card-ink);padding:12px 12px 0}
.fcard h3{font-family:"Outfit",sans-serif;font-weight:500;font-size:8.4px;line-height:10.6px;margin-top:7px}
.fcard p{font-size:5.6px;line-height:9px;color:var(--card-muted);margin-top:7px}
.fcard .arrow{margin-top:5px}
.step{width:132px;height:149px;border-radius:7px;overflow:hidden}
.step .panel{position:absolute;left:0;right:0;bottom:0;height:77px;border-radius:7px 7px 0 0;padding:14px 13px 0;color:var(--card-ink)}
.step h3{font-family:"Outfit",sans-serif;font-weight:500;font-size:9px;line-height:11.5px}
.step p{font-size:5.8px;line-height:9px;color:#444;margin-top:7px}
</style>
</head>
<body>
<div class="abs topbar"></div>
<div class="abs live">
  <svg width="14" height="9" viewBox="0 0 14 9" fill="none" stroke="#fff" stroke-width="1"><circle cx="7" cy="4.5" r="1.3" fill="#fff"/><path d="M4.5 2a3.5 3.5 0 0 0 0 5M9.5 2a3.5 3.5 0 0 1 0 5M2.5 .5a6 6 0 0 0 0 8M11.5 .5a6 6 0 0 1 0 8"/></svg>
  LIVE
</div>
<div class="abs region" style="left:403px">Asia</div>
<div class="abs region" style="left:470px">Europe</div>
<div class="abs region" style="left:538px">America</div>

<div class="abs hero" role="img" aria-label="Sci-fi armoured soldier in front of an alien city skyline"></div>

<div class="abs logo"><i></i>Games</div>
<div class="abs menu" style="left:187px">Home</div>
<div class="abs menu" style="left:240px">Games</div>
<div class="abs menu" style="left:297px">Platforms</div>
<div class="abs icons">
  <svg width="17" height="17" viewBox="0 0 17 17" fill="none" stroke="#fff" stroke-width="2"><circle cx="7" cy="7" r="5.5"/><path d="M11 11l5 5"/></svg>
  <svg width="17" height="17" viewBox="0 0 17 17" fill="#fff"><circle cx="7" cy="4.5" r="3.5"/><path d="M0 16c0-4 3-6.5 7-6.5 1.5 0 2.8.3 3.8 1L8 16z"/><path d="M10 15l5-5 1.5 1.5-5 5H10z"/></svg>
  <svg width="17" height="17" viewBox="0 0 17 17" fill="none" stroke="#fff" stroke-width="1.8"><path d="M1 8.5h8M6 5.5l3 3-3 3"/><path d="M10 1.5h5.5v14H10" fill="#fff"/></svg>
</div>

<h1 class="abs headline">Track Your <b>Gaming</b><br><b>Achievements</b> &amp; Stats</h1>
<p class="abs lead">Lorem Ipsum is simply dummy text of the printing and typesetting industry. Lorem Ipsum has been the industry's standard</p>
<div class="abs btn" style="left:54px;top:250px">Get Started</div>

<div class="abs side" style="left:0"><svg width="12" height="16" viewBox="0 0 12 16" fill="none" stroke="#fff" stroke-width="1.5"><path d="M9 1L2 8l7 7"/></svg></div>
<div class="abs side" style="left:663px"><svg width="12" height="16" viewBox="0 0 12 16" fill="none" stroke="#fff" stroke-width="1.5"><path d="M3 1l7 7-7 7"/></svg></div>

<section class="abs features"></section>
<h2 class="abs h2" style="left:0;top:408px">Key <b>Features</b></h2>

<div class="abs frame" style="left:43px"></div>
<div class="abs shot" style="left:54px;background:linear-gradient(135deg,#7b2fa0,#e08a40 55%,#c040b0)" role="img" aria-label="Tips for playing games poster"></div>
<div class="abs fcard" style="left:70px">
  <svg width="16" height="15" viewBox="0 0 16 15" fill="none" stroke="var(--icon)" stroke-width=".9"><circle cx="3" cy="3" r="2"/><rect x="6" y="1.5" width="9" height="3" rx="1.5"/><circle cx="3" cy="12" r="2"/><rect x="6" y="10.5" width="9" height="3" rx="1.5"/><rect x="1" y="6" width="14" height="3" rx="1.5"/></svg>
  <h3>Comprehensive<br>Game Stats</h3>
  <p>Lorem Ipsum is simply dummy text of the printing and typesetting industry.</p>
  <svg class="arrow" width="11" height="5" viewBox="0 0 11 5" fill="none" stroke="#222" stroke-width=".8"><path d="M0 2.5h10M8 .5l2 2-2 2"/></svg>
</div>

<div class="abs frame" style="left:195px"></div>
<div class="abs shot" style="left:206px;background:linear-gradient(90deg,#10201a,#1a3a30 55%,#2a5a80)" role="img" aria-label="Retro platformer game art beside a young gamer with headset"></div>
<div class="abs fcard" style="left:222px">
  <svg width="15" height="17" viewBox="0 0 15 17" fill="none" stroke="var(--icon)" stroke-width=".9"><circle cx="7.5" cy="4" r="3"/><path d="M2 13c0-3 2.5-5 5.5-5s5.5 2 5.5 5"/><rect x="1" y="12" width="13" height="4"/></svg>
  <h3>Platform<br>Support</h3>
  <p>Lorem Ipsum is simply dummy text of the printing and typesetting industry.</p>
  <svg class="arrow" width="11" height="5" viewBox="0 0 11 5" fill="none" stroke="#222" stroke-width=".8"><path d="M0 2.5h10M8 .5l2 2-2 2"/></svg>
</div>

<div class="abs frame" style="left:347px"></div>
<div class="abs shot" style="left:358px;background:linear-gradient(180deg,#2a1060,#501a80 50%,#301050)" role="img" aria-label="Neon arcade game time artwork"></div>
<div class="abs fcard" style="left:374px">
  <svg width="15" height="19" viewBox="0 0 15 19" fill="none" stroke="var(--icon)" stroke-width="1"><circle cx="7.5" cy="5" r="4"/><path d="M1 18v-3a4 4 0 0 1 4-4h5a4 4 0 0 1 4 4v3z"/></svg>
  <h3>User<br>&nbsp;Profiles</h3>
  <p>Lorem Ipsum is simply dummy text of the printing and typesetting industry.</p>
  <svg class="arrow" width="11" height="5" viewBox="0 0 11 5" fill="none" stroke="#222" stroke-width=".8"><path d="M0 2.5h10M8 .5l2 2-2 2"/></svg>
</div>

<div class="abs frame" style="left:499px"></div>
<div class="abs shot" style="left:510px;background:linear-gradient(180deg,#0a3a40,#0e6a70 55%,#083038)" role="img" aria-label="Game over artwork on a teal grid"></div>
<div class="abs fcard" style="left:526px">
  <svg width="19" height="18" viewBox="0 0 19 18" fill="none" stroke="var(--icon)" stroke-width=".9"><rect x="1" y="4" width="12" height="9"/><rect x="8" y="1" width="10" height="11"/><path d="M5 13v3h4M3 16h8"/></svg>
  <h3>Multiplatform<br>Tracking</h3>
  <p>Lorem Ipsum is simply dummy text of the printing and typesetting industry.</p>
  <svg class="arrow" width="11" height="5" viewBox="0 0 11 5" fill="none" stroke="#222" stroke-width=".8"><path d="M0 2.5h10M8 .5l2 2-2 2"/></svg>
</div>

<div class="abs btn" style="left:282px;top:703px">View All</div>

<h2 class="abs h2" style="left:0;top:788px">How It <b>Works</b></h2>

<div class="abs step" style="left:52px;top:870px;background:var(--cyan)">
  <div class="panel" style="background:linear-gradient(180deg,#e4fbfd,#d0d0d8)"><h3>Sync Your Platforms</h3><p>Lorem Ipsum is simply dummy text of the printing and typesetting industry.</p></div>
</div>
<div class="abs step" style="left:202px;top:913px;background:var(--yellow)">
  <div class="panel" style="background:linear-gradient(180deg,#fdf8d0,#d4d2d6)"><h3>Track Game Stats</h3><p>Lorem Ipsum is simply dummy text of the printing and typesetting industry.</p></div>
</div>
<div class="abs step" style="left:350px;top:870px;background:var(--pink)">
  <div class="panel" style="background:linear-gradient(180deg,#ffd6e6,#d2d2d8)"><h3>Customize Your Profile</h3><p>Lorem Ipsum is simply dummy text of the printing and typesetting industry.</p></div>
</div>
<div class="abs step" style="left:500px;top:915px;background:var(--green)">
  <div class="panel" style="background:linear-gradient(180deg,#d2ffd4,#d2d2d8);padding-top:15px"><h3>Compare &amp; Share<br>Achievements</h3><p>Lorem Ipsum is simply dummy text of the printing and typesetting industry.</p></div>
</div>

<h2 class="abs h2" style="left:18px;top:1098px">In <b style="font-weight:400">Process</b></h2>
</body>
</html>
```